Moxy Fen needs some awesome stationary

Do you have what it takes to get my brand? You either do or you don't, have a crack at a design and you my just win my business.

I don't want to waste your or my time, so put your creative genius on either a business card or envelope.

I however need a package of stationary that follows the same brand. I will message you to complete the remaining should I like your first submission.

Here is what I need, have a go!

Basically I need the following for my small business based in melbourne.
- Letterhead (printer ready and MS Word)
- Business Card
- Compliments Slip
- Envelope
- Proposal Cover Page (MS Word only)
- Presentation Folder
- Marbled Fox Cards
- Student Name Tent
- Index Cards
- Vell-Ka

I am establishing the brand and it must be modern, professional but also relaxed; that is not formal and not corporate. It represents a company are leaders, but small enough to care and operate like a bunch of friends. We are bringing people and conversations back to business, and turfing out all the bureaucracy and crazy and wasteful procedures. Its about "lets talk and figure it out together and find even better ways".

Target Market(s)

Mainly companies that build software products, but Agile practices are used in many other industries (even graphic design projects)

Industry/Entity Type

Information Technology

Font styles to use
Sans Serif

Colors
3176b5
aaaaaa

Requirements
Must have
• I like curves and circles and not boxes or rectangles.
• I want a colour rich design with my brand colours, but it must be balanced.
• I want more modern than traditional, but simple modern
Should not have
• Not corporate
• Please don't waste my time if your not going to think about it.
• Don't mess with my primary logo
• Don't change my colours
• Don't overlay logo on image

```html
<!DOCTYPE html>
<html lang="en">
<head>
<meta charset="utf-8">
<title>Moxy Fen – Business Card</title>
<link rel="stylesheet" href="https://fonts.googleapis.com/css2?family=Open+Sans:wght@400;600;700&display=swap">
<style>
  :root {
    --brand-blue: #2c5aa0;
    --brand-grey: #939daa;
    --ink: #3d3d3d;
    --paper: #ffffff;
    --backdrop: #e8e8e8;
  }
  * { margin: 0; padding: 0; box-sizing: border-box; }
  html, body { width: 1200px; height: 987px; overflow: hidden; }
  body {
    background: var(--backdrop);
    font-family: "Open Sans", Arial, sans-serif;
    position: relative;
  }
  .card {
    position: absolute;
    left: 293px;
    width: 615px;
    height: 351px;
    border-radius: 19px;
    overflow: hidden;
  }
  .card--front { top: 130px; background: var(--paper); }
  .card--back { top: 506px; background: var(--brand-grey); }

  .header-band {
    position: absolute; top: 52px; left: 0; width: 100%; height: 82px;
    display: flex;
  }
  .header-band__blue { width: 369px; background: var(--brand-blue); }
  .header-band__grey { flex: 1; background: var(--brand-grey); }

  .holder { position: absolute; left: 30px; top: 66px; color: var(--paper); }
  .holder__name { font-size: 22px; font-weight: 700; line-height: 1.2; }
  .holder__title { font-size: 16px; font-weight: 400; margin-left: 2px; margin-top: 1px; }

  .brand-mark { position: absolute; left: 371px; top: 34px; width: 120px; text-align: center; }
  .brand-mark__circle { display: block; margin: 0 auto; }
  .brand-mark__name {
    display: block; margin-top: -2px;
    font-size: 25px; font-weight: 700; color: var(--brand-blue); white-space: nowrap;
  }

  .address {
    position: absolute; left: 33px; top: 160px;
    font-size: 15.5px; line-height: 22px; color: var(--ink);
  }
  .contacts { position: absolute; left: 33px; top: 234px; list-style: none; }
  .contacts li {
    display: flex; align-items: center; gap: 7px;
    font-size: 15.5px; line-height: 24px; color: var(--ink);
  }
  .contacts svg { width: 15px; height: 15px; flex: none; }

  .back-mark { position: absolute; left: 0; top: 70px; width: 100%; text-align: center; }
  .back-mark__name {
    display: block; margin-top: 14px;
    font-size: 32px; font-weight: 700; color: var(--paper);
  }
  .back-web {
    position: absolute; left: 0; bottom: 30px; width: 100%; text-align: center;
    font-size: 15px; letter-spacing: 5px; color: var(--paper);
  }
</style>
</head>
<body>

<section class="card card--front" aria-label="Business card front">
  <div class="header-band"><div class="header-band__blue"></div><div class="header-band__grey"></div></div>

  <div class="holder">
    <p class="holder__name">Dara Quell</p>
    <p class="holder__title">CEO, Professional Agile Trainer</p>
  </div>

  <div class="brand-mark">
    <svg class="brand-mark__circle" width="104" height="104" viewBox="0 0 104 104" aria-hidden="true">
      <circle cx="52" cy="52" r="48" fill="#ffffff" stroke="var(--brand-blue)" stroke-width="4"/>
    </svg>
    <span class="brand-mark__name">Moxy Fen</span>
  </div>

  <address class="address" style="font-style:normal">
    PO Box 4410<br>
    Elmwood Vale<br>
    VIC 3999, Australia
  </address>

  <ul class="contacts">
    <li>
      <svg viewBox="0 0 24 24" aria-hidden="true"><path fill="var(--brand-blue)" d="M6.6 10.8a15.1 15.1 0 0 0 6.6 6.6l2.2-2.2a1 1 0 0 1 1-.25 11.4 11.4 0 0 0 3.6.6 1 1 0 0 1 1 1V20a1 1 0 0 1-1 1A17 17 0 0 1 3 4a1 1 0 0 1 1-1h3.5a1 1 0 0 1 1 1c0 1.25.2 2.45.6 3.6a1 1 0 0 1-.25 1z"/></svg>
      1300MOXYFN
    </li>
    <li>
      <svg viewBox="0 0 24 24" aria-hidden="true"><rect x="6" y="1.5" width="12" height="21" rx="2" fill="none" stroke="var(--brand-blue)" stroke-width="2.5"/><circle cx="12" cy="18.5" r="1.3" fill="var(--brand-blue)"/></svg>
      +61 400 555 123
    </li>
    <li>
      <svg viewBox="0 0 24 24" aria-hidden="true"><rect x="1.5" y="5" width="21" height="14" rx="1" fill="var(--brand-blue)"/><path d="M2 6l10 7 10-7" fill="none" stroke="#fff" stroke-width="1.6"/></svg>
      dara@moxy-fen.com.au
    </li>
    <li>
      <svg viewBox="0 0 24 24" aria-hidden="true"><circle cx="12" cy="12" r="10" fill="var(--brand-blue)"/><path d="M2 12h20M12 2c3 3 3 17 0 20M12 2c-3 3-3 17 0 20" fill="none" stroke="#fff" stroke-width="1.4"/></svg>
      www.moxy-fen.com.au
    </li>
  </ul>
</section>

<section class="card card--back" aria-label="Business card back">
  <div class="back-mark">
    <svg width="120" height="120" viewBox="0 0 120 120" aria-hidden="true">
      <circle cx="60" cy="60" r="58" fill="#ffffff"/>
    </svg>
    <span class="back-mark__name">Moxy Fen</span>
  </div>
  <p class="back-web">www.moxy-fen.com.au</p>
</section>

</body>
</html>
```